OrvanoGoodsHub.com -Ecommerce Website for Luxury Products

This will be an ecommerce site. A website portal that will allow both consumers to enter one way and see specific purchase options and businesses to enter via a different link that allows B2B to see their specific options once logged into. B2C can purchase both as a guest/or after account is setup. B2B must be approved to set up account. This is front end website project. Back-end integration is separate. Will be hosted on Servantia with a domain registration held at Pexadrinet. Additional website concept/idea/synergy can be found from sister site-KRWZHospitality.com

```html
<!DOCTYPE html>
<html lang="en">
<head>
<meta charset="utf-8">
<title>OrvanoGoods – Online Store</title>
<link href="https://fonts.googleapis.com/css2?family=Libre+Baskerville:wght@400;700&family=Poppins:wght@300;400;500&display=swap" rel="stylesheet">
<style>
:root{
  --gold:#8a6a4a;
  --bronze:#94704d;
  --cocoa:#6b5847;
  --tan:#a07e62;
  --ink:#1b1b1b;
  --cream:#f4f2ed;
  --mist:#f1eeec;
  --line:#8d7560;
  --white:#ffffff;
  --star:#f2c200;
}
*{box-sizing:border-box;margin:0;padding:0}
html,body{width:1200px;height:3857px;overflow:hidden;background:var(--white)}
body{position:relative;font-family:"Poppins",sans-serif;color:var(--ink)}
.abs{position:absolute}
.serif{font-family:"Libre Baskerville",serif}

/* header */
.menu{left:160px;top:46px;display:flex;align-items:center;gap:10px;font-family:"Libre Baskerville",serif;font-size:13px;color:var(--gold);letter-spacing:.5px}
.brand-mark{left:0;width:1200px;top:40px;text-align:center;font-family:"Libre Baskerville",serif;font-weight:700;font-size:24px;color:var(--gold)}
.btn-outline{display:flex;align-items:center;justify-content:center;border:2px solid #555;font-size:13px;letter-spacing:.5px;color:#333}
.contact-btn{left:855px;top:37px;width:183px;height:40px}

/* hero */
.hero{left:0;top:112px;width:1200px;height:603px;background:linear-gradient(100deg,#3a1f1c 0%,#5a2c2a 30%,#6e3a3a 55%,#4a2b2d 75%,#2a1b1d 100%)}
.hero-band{left:262px;top:245px;width:676px;height:325px;background:rgba(20,12,12,.55)}
.hero-small{left:0;top:288px;width:1200px;text-align:center;font-size:50px;color:var(--white)}
.hero-title{left:0;top:333px;width:1200px;text-align:center;font-size:82px;font-weight:700;color:var(--white)}
.hero-text{left:0;top:428px;width:1200px;text-align:center;font-size:12.5px;line-height:15px;color:var(--white);letter-spacing:.3px}
.hero-btn{left:508px;top:481px;width:184px;height:39px;border:1.5px solid #bbb;color:var(--white);font-size:13px;font-weight:500;display:flex;align-items:center;justify-content:center}

/* portal cards */
.portal{top:631px;width:423px;height:169px;border-radius:10px;text-align:center;padding-top:25px;box-shadow:0 6px 14px rgba(0,0,0,.12)}
.portal h3{font-family:"Libre Baskerville",serif;font-size:22px;font-weight:700;margin-bottom:8px}
.portal p{font-size:13px;line-height:19px;width:260px;margin:0 auto}
.portal .pbtn{position:absolute;top:104px;width:188px;height:40px;color:var(--white);font-size:13px;display:flex;align-items:center;justify-content:center}
.portal.consumer{left:162px;background:var(--mist)}
.portal.consumer .pbtn{left:117px;background:#6b5545}
.portal.business{left:615px;background:var(--ink);color:var(--white)}
.portal.business .pbtn{left:117px;background:var(--bronze)}

/* about */
.rule{height:1.5px;background:var(--line)}
.about{left:185px;top:906px;width:831px;height:325px;background:var(--cream);border:1.5px solid #b8b2aa;text-align:center}
.about h2{font-family:"Libre Baskerville",serif;font-size:42px;font-weight:700;margin-top:22px}
.about p{font-size:13px;line-height:19.5px;width:750px;margin:20px auto 0;color:#333}
.about .btn-outline{position:absolute;left:322px;top:246px;width:188px;height:41px;border:1.5px solid #777;color:#555}
.glass{left:142px;top:1100px;width:143px;height:242px;border-radius:20px 20px 40px 40px;background:linear-gradient(180deg,#dfe6ea 0%,#e9a24a 40%,#b5561e 70%,#c9d4da 100%)}

/* feature rows */
.photo{background:linear-gradient(135deg,#2e2a26,#7a5a3c 45%,#c2803f 60%,#3a342e)}
.feature{color:var(--white)}
.feature h3{font-family:"Libre Baskerville",serif;font-size:34px;font-weight:700;margin-bottom:14px}
.feature p{font-size:13.5px;line-height:19.5px}
.rating{display:flex;align-items:center;gap:12px;font-size:14px;margin-top:28px}
.stars{color:var(--star);font-size:16px;letter-spacing:2px}
.shop-link{display:inline-flex;align-items:center;gap:22px;font-size:14px;font-weight:500;margin-top:14px;padding-bottom:4px;border-bottom:1.5px solid var(--white)}

/* video */
.video{left:0;top:2488px;width:1200px;height:372px;background:linear-gradient(180deg,#3f4a6a 0%,#2d3350 40%,#2a201e 75%,#1a1412 100%)}
.play{left:573px;top:2647px;width:54px;height:54px;border-radius:50%;background:rgba(255,255,255,.85);display:flex;align-items:center;justify-content:center}

/* product tiles */
.tile{top:2937px;width:341px;height:426px}
.tile .shade{position:absolute;left:15px;right:15px;top:228px;height:172px;background:rgba(10,8,6,.7);text-align:center;color:var(--white)}
.tile h4{font-family:"Libre Baskerville",serif;font-size:27px;font-weight:700;margin-top:12px}
.tile .bar{width:46px;height:2px;background:var(--white);margin:12px auto 14px}
.tile .stars{font-size:15px}
.tile .rt{font-size:13.5px;margin-top:2px}
.tbtn{position:absolute;left:76px;top:363px;width:188px;height:39px;background:var(--white);color:#222;font-size:13px;display:flex;align-items:center;justify-content:center}

/* footer */
.footer{left:0;top:3535px;width:1200px;height:322px;background:#000;color:var(--white)}
.seal{left:513px;top:3453px;width:174px;height:174px;border-radius:50%;background:#0a0a0a;border:4px solid var(--bronze);display:flex;align-items:center;justify-content:center;font-family:"Libre Baskerville",serif;font-weight:700;font-size:24px;color:var(--bronze)}
.fnav{top:3676px;font-size:14px;color:var(--white)}
.fcontact{top:3734px;display:flex;align-items:center;gap:12px;font-size:14px;color:var(--white)}
.ficon{width:28px;height:28px;border-radius:50%;background:var(--bronze);display:flex;align-items:center;justify-content:center}
.copy{left:220px;top:3818px;font-size:12.5px;color:var(--white)}
.social{top:3816px;width:16px;height:16px;border-radius:50%;border:1.5px solid var(--white)}
</style>
</head>
<body>

<!-- header -->
<div class="abs menu">
  <svg width="20" height="14" viewBox="0 0 20 14"><path d="M0 1h20M0 7h14M0 13h20" stroke="#8a6a4a" stroke-width="1.6"/></svg>
  MENU
</div>
<div class="abs brand-mark">Orvano</div>
<div class="abs btn-outline contact-btn">CONTACT US</div>

<!-- hero -->
<div class="abs hero" role="img" aria-label="Photo of a bearded man exhaling smoke in a dimly lit speakeasy bar"></div>
<div class="abs hero-band"></div>
<div class="abs hero-small serif">Welcome To</div>
<div class="abs hero-title serif">OrvanoGoods</div>
<div class="abs hero-text">A speakeasy, also called a blind pig or blind tiger, is an illicit establishment<br>that sells alcoholic beverages, or a retro style bar that replicates aspects of historical speakeasies.</div>
<div class="abs hero-btn">SHOP NOW</div>

<div class="abs portal consumer">
  <h3>Shop As A Consumer</h3>
  <p>Browse and Purchase Directly As A Individual.</p>
  <div class="pbtn">SHOP AS A CONSUMER</div>
</div>
<div class="abs portal business">
  <h3>Business Portal</h3>
  <p>Log In Or Apply For A B2B Account To Access Bulk Pricing.</p>
  <div class="pbtn">BUSINESS PORTAL</div>
</div>

<!-- about -->
<div class="abs rule" style="left:0;top:875px;width:383px"></div>
<div class="abs about">
  <h2>About Us</h2>
  <p>it over 1920 years. Edmund Harrow, a Latin professor at Alderbrook College in Virginia, looked up one of the more obscure Latin words, consectetur, from a Lorem Ipsum passage, and going through the cites of the word in classical literature, discovered the undoubtable source. Lorem Ipsum comes from sections 1.10.32 and 1.10.33 of "de Finibus Bonorum et Malorum" (The Extremes of Good and Evil) by Varenius, it over 2000 years old. Edmund Harrow, a Latin professor at Alderbrook College, looked up one of the more obscure Latin words, consectetur, from a Lorem Ipsum passage, and Finibus.</p>
  <div class="btn-outline">LEARN MORE</div>
</div>
<div class="abs glass" role="img" aria-label="Crystal tumbler of amber cocktail with orange peel"></div>
<div class="abs rule" style="left:600px;top:1284px;width:600px"></div>

<!-- fragrances row -->
<div class="abs" style="left:527px;top:1468px;width:600px;height:396px;background:var(--cocoa)"></div>
<div class="abs photo" style="left:72px;top:1396px;width:600px;height:395px" role="img" aria-label="Bartender pouring an amber drink through a strainer into two glasses"></div>
<div class="abs feature" style="left:739px;top:1512px;width:332px">
  <h3>Fragrances</h3>
  <p>it over 1920 years. Edmund Harrow, a Latin professor at Alderbrook College in Virginia, looked up one of the more obscure Latin words, consectetur, from a Lorem Ipsum passage, and going through the cites of the word in classical literature, discovered the undoubtable source. Lorem Ipsum comes from sections.</p>
  <div class="rating"><span class="stars">★★★★★</span>5 Star Rating</div>
  <div class="shop-link">Shop Now <svg width="16" height="8" viewBox="0 0 16 8"><path d="M0 4h15M11 1l4 3-4 3" stroke="#fff" fill="none" stroke-width="1.3"/></svg></div>
</div>

<!-- cigar row -->
<div class="abs" style="left:72px;top:1942px;width:600px;height:395px;background:var(--tan)"></div>
<div class="abs feature" style="left:117px;top:2000px;width:366px">
  <h3>Cigar</h3>
  <p>it over 1920 years. Edmund Harrow, a Latin professor at Alderbrook College in Virginia, looked up one of the more obscure Latin words, consectetur, from a Lorem Ipsum passage, and going through the cites of the word in classical literature, discovered the undoubtable source. Lorem Ipsum comes from sections.</p>
  <div class="rating"><span class="stars">★★★★★</span>5 Star Rating</div>
  <div class="shop-link">Shop Now <svg width="16" height="8" viewBox="0 0 16 8"><path d="M0 4h15M11 1l4 3-4 3" stroke="#fff" fill="none" stroke-width="1.3"/></svg></div>
</div>
<div class="abs" style="left:527px;top:2017px;width:600px;height:395px;background:linear-gradient(160deg,#8c6a45,#4a2a1c 45%,#1c120e 70%,#b08a3e)" role="img" aria-label="Open box of premium cigars with gold bands"></div>

<!-- video -->
<div class="abs video" role="img" aria-label="Interior of a cigar lounge with leather chairs and round tables"></div>
<div class="abs play"><svg width="16" height="18" viewBox="0 0 16 18"><path d="M2 1l13 8-13 8z" fill="#555"/></svg></div>

<!-- product tiles -->
<div class="abs tile" style="left:60px;background:linear-gradient(160deg,#3a3734,#6a4428 50%,#1e1a18)" role="img" aria-label="Smoldering cigar close-up">
  <div class="shade"><h4>Cigar Accessories</h4><div class="bar"></div><div class="stars">★★★★★</div><div class="rt">5 Star Rating</div></div>
  <div class="tbtn">SHOP NOW</div>
</div>
<div class="abs tile" style="left:430px;background:linear-gradient(160deg,#2c2a28,#5b5650 50%,#1a1816)" role="img" aria-label="Crystal fragrance decanter with strainer">
  <div class="shade"><h4>Fragrances</h4><div class="bar"></div><div class="stars">★★★★★</div><div class="rt">5 Star Rating</div></div>
  <div class="tbtn">SHOP NOW</div>
</div>
<div class="abs tile" style="left:800px;background:linear-gradient(160deg,#23282a,#9a7a2e 50%,#3a2a1c)" role="img" aria-label="Glass bottle of oil with cork and spices">
  <div class="shade"><h4>Oils</h4><div class="bar"></div><div class="stars">★★★★★</div><div class="rt">5 Star Rating</div></div>
  <div class="tbtn">SHOP NOW</div>
</div>

<!-- footer -->
<div class="abs footer"></div>
<div class="abs seal">Orvano</div>
<div class="abs fnav" style="left:374px">Home</div>
<div class="abs fnav" style="left:488px">About Us</div>
<div class="abs fnav" style="left:618px">Products</div>
<div class="abs fnav" style="left:751px">Contact Us</div>

<div class="abs fcontact" style="left:284px">
  <span class="ficon"><svg width="14" height="14" viewBox="0 0 24 24"><path d="M6.6 10.8a15 15 0 006.6 6.6l2.2-2.2a1 1 0 011-.25 11.4 11.4 0 003.6.6 1 1 0 011 1V20a1 1 0 01-1 1A17 17 0 013 4a1 1 0 011-1h3.5a1 1 0 011 1c0 1.25.2 2.45.6 3.6a1 1 0 01-.25 1z" fill="#fff"/></svg></span>
  + 1 555 010 2048
</div>
<div class="abs fcontact" style="left:480px">
  <span class="ficon"><svg width="14" height="11" viewBox="0 0 14 11"><rect x=".5" y=".5" width="13" height="10" fill="none" stroke="#fff"/><path d="M.5.5l6.5 5 6.5-5" fill="none" stroke="#fff"/></svg></span>
  orvanogoods1234@mailbox.test
</div>
<div class="abs fcontact" style="left:763px">
  <span class="ficon"><svg width="12" height="15" viewBox="0 0 12 15"><path d="M6 0a6 6 0 00-6 6c0 4.5 6 9 6 9s6-4.5 6-9a6 6 0 00-6-6zm0 8.2a2.2 2.2 0 110-4.4 2.2 2.2 0 010 4.4z" fill="#fff"/></svg></span>
  122, Lorem ipsum dolird
</div>

<div class="abs copy">Copyright©2025OrvanoGoods. All rights reserved.</div>
<div class="abs social" style="left:878px"></div>
<div class="abs social" style="left:921px"></div>
<div class="abs social" style="left:964px"></div>

</body>
</html>
```